Photographer website, needs Facebook design. (updated details in brief.)

Company name Tobin Velasco Photography, looking to add a Facebook design, that is minimalistic, yet powerful. Less is more in my opinion, but what's there is creative, but eye catchy. see example image in files section for a better idea of what I am looking for. I have also added some source files for my logo.

Target Market(s)

local musicians/artists, models/fashion, and business professional looking for headshots or corporate business profile images.

Colors
0655a3
cfdfed
ffffff

Requirements
Must have
• I have added a screen shot of what I am looking for, for everyone to gain a better sense of my vision. Please see the uploaded files below.
Nice to have
• I am really a fan of the example image in the files section below. Something close to that I would be very happy with.
Should not have
• should not have my face on the cover.

```html
<!DOCTYPE html>
<html lang="en">
<head>
<meta charset="utf-8">
<title>Tobin Velasco Photography – Cover</title>
<link rel="stylesheet" href="https://fonts.googleapis.com/css2?family=Josefin+Sans:wght@400;600;700&display=swap">
<style>
  :root {
    --sun: #f4e035;
    --sky: #bbf0fc;
    --ink: #0c0c0c;
    --art-dark: #2b2a1c;
    --art-light: #e2cf33;
  }
  html, body {
    margin: 0;
    padding: 0;
    overflow: hidden;
    background: #ffffff;
  }
  .cover {
    position: relative;
    width: 1200px;
    height: 457px;
    overflow: hidden;
    background: var(--sky);
    font-family: "Josefin Sans", sans-serif;
    color: var(--ink);
  }
  .top-band {
    position: absolute;
    left: 0; top: 0;
    width: 1200px; height: 184px;
    background: var(--sun);
  }
  .center-stage {
    position: absolute;
    left: 311px; top: 0;
    width: 595px; height: 280px;
    background: var(--sun);
  }
  .desk-line {
    position: absolute;
    left: 350px; top: 277px;
    width: 518px; height: 2px;
    background: var(--ink);
  }
  .mascot-art {
    position: absolute;
    left: 394px; top: 56px;
    width: 382px; height: 250px;
    background: linear-gradient(135deg, var(--art-dark) 0%, #6d6526 45%, var(--art-light) 100%);
    border-radius: 4px;
  }
  .intro-quote {
    position: absolute;
    left: 23px; top: 28px;
    width: 288px;
    margin: 0;
    font-size: 12px;
    line-height: 14.7px;
    letter-spacing: 1.9px;
    text-align: justify;
    text-align-last: left;
    font-weight: 400;
  }
  .intro-quote .sign-off {
    display: block;
    text-align: right;
    text-align-last: right;
  }
  .brand {
    position: absolute;
    right: 22px; top: 32px;
    margin: 0;
    text-align: right;
    font-weight: 600;
    line-height: 1;
  }
  .brand-name {
    display: block;
    font-size: 44px;
    letter-spacing: 6px;
  }
  .brand-trade {
    display: block;
    margin-top: 8px;
    margin-right: 54px;
    font-size: 33px;
    font-weight: 700;
    letter-spacing: 5px;
  }
  .tagline {
    position: absolute;
    left: 318px; top: 319px;
    width: 592px;
    margin: 0;
    font-size: 23px;
    font-weight: 700;
    letter-spacing: 3.6px;
    white-space: nowrap;
  }
</style>
</head>
<body>
  <main class="cover">
    <div class="top-band"></div>
    <div class="center-stage"></div>
    <div class="mascot-art" role="img" aria-label="Illustration of a striped cat peeking over a ledge while holding a camera"></div>
    <div class="desk-line"></div>

    <p class="intro-quote">
      I know what I can bring to the table. It's confidence, professionalism, and dedication to quality, and its what I bring every time. If these are qualities you look for in a photographer, then you've come to the right place. We won't disappoint, and we look forward to hearing from you.
      <span class="sign-off">-Tobin</span>
    </p>

    <h1 class="brand">
      <span class="brand-name">TOBIN VELASCO</span>
      <span class="brand-trade">PHOTOGRAPHY</span>
    </h1>

    <p class="tagline">WE LOOK FORWARD TO HEARING FROM YOU.</p>
  </main>
</body>
</html>
```